first fantastic look and impression

We are looking for a concept for letterhead, business card, emailfooter and template for invoices or offers for our company in the consultation business.
The dancer is a symbol who we are: it looks simple, but there is a lot of hard work and many years of training in this movement. The look is also what we want: elegant, modern, strong, with a touch of extravaganza
Target Market(s)
Hotelbusiness , Consulting
Font styles to use
Sans Serif
Other font styles liked:
- please give us a option we are open
Requirements
Must have
- We are not typical consultants but sparring partners and coaches for the hotel and that should also be expressed in the design. Maybe there is an icon that supports the whole thing. We are more modern and bolder than our industry colleagues.
we are modern, fresh, agile, fast
Nice to have
- a icon

```html
<!DOCTYPE html>
<html lang="en">
<head>
<meta charset="utf-8">
<title>Brennwald+Partner – Business Card</title>
<link rel="stylesheet" href="https://fonts.googleapis.com/css2?family=Cormorant+Garamond:wght@400;500&family=Montserrat:wght@400;700&display=swap">
<style>
  :root {
    --stage: #8ea6b9;
    --card-blue-deep: #4b7396;
    --card-blue-light: #7c9fba;
    --paper: #ffffff;
    --ink-white: #ffffff;
    --ink-steel: #5f7f9c;
    --ink-grey: #6f7a84;
    --ink-navy: #2f5b82;
    --figure-tone: #e4e7ea;
    --figure-tone-soft: #f3f4f5;
  }
  * { box-sizing: border-box; margin: 0; padding: 0; }
  html, body { width: 1200px; height: 914px; overflow: hidden; }
  body {
    background: var(--stage);
    display: flex;
    align-items: center;
    justify-content: center;
    gap: 70px;
  }
  .card {
    width: 330px;
    height: 530px;
    position: relative;
    box-shadow: 0 18px 40px rgba(40, 60, 80, 0.28);
    overflow: hidden;
  }

  /* Front side */
  .card--front {
    background: linear-gradient(135deg, var(--card-blue-deep) 0%, var(--card-blue-light) 100%);
    color: var(--ink-white);
    text-align: center;
  }
  .front__wordmark {
    position: absolute;
    top: 150px;
    left: 0; right: 0;
    font-family: "Cormorant Garamond", serif;
    font-weight: 400;
    font-size: 30px;
    letter-spacing: 0.5px;
  }
  .front__person {
    position: absolute;
    top: 300px;
    left: 0; right: 0;
    font-family: "Montserrat", sans-serif;
  }
  .person__name { font-weight: 700; font-size: 16px; letter-spacing: 0.3px; }
  .person__role { font-weight: 400; font-size: 12px; margin-top: 4px; letter-spacing: 0.4px; }
  .front__tagline {
    position: absolute;
    bottom: 60px;
    left: 0; right: 0;
    font-family: "Cormorant Garamond", serif;
    font-size: 15px;
    letter-spacing: 0.4px;
  }

  /* Back side */
  .card--back { background: var(--paper); }
  .back__wordmark {
    position: absolute;
    top: 70px;
    left: 0; right: 0;
    text-align: center;
    font-family: "Cormorant Garamond", serif;
    font-weight: 400;
    font-size: 30px;
    color: var(--ink-steel);
  }
  .back__figure {
    position: absolute;
    left: 30px;
    top: 180px;
    width: 270px;
    height: 230px;
    border-radius: 40% 50% 45% 55%;
    background: radial-gradient(ellipse at 50% 45%, var(--figure-tone) 0%, var(--figure-tone-soft) 60%, var(--paper) 100%);
  }
  .back__contacts {
    position: absolute;
    top: 235px;
    left: 0; right: 0;
    display: flex;
    flex-direction: column;
    align-items: center;
    gap: 14px;
    font-family: "Montserrat", sans-serif;
    font-size: 13px;
    color: var(--ink-grey);
  }
  .contact {
    display: flex;
    flex-direction: column;
    align-items: center;
    gap: 5px;
  }
  .contact--location { color: var(--ink-navy); font-weight: 700; }
  .contact__icon { width: 14px; height: 14px; }
</style>
</head>
<body>

  <article class="card card--back" aria-label="Business card back">
    <div class="back__wordmark">Brennwald+Partner</div>
    <div class="back__figure" role="img" aria-label="Faint photograph of a dancer in motion"></div>
    <div class="back__contacts">
      <div class="contact contact--location">
        <svg class="contact__icon" viewBox="0 0 14 14" aria-hidden="true">
          <circle cx="7" cy="7" r="7" fill="var(--ink-steel)"/>
          <path d="M7 3.2a2.4 2.4 0 0 0-2.4 2.4C4.6 7.4 7 10.6 7 10.6s2.4-3.2 2.4-5A2.4 2.4 0 0 0 7 3.2z" fill="#fff"/>
          <circle cx="7" cy="5.6" r="0.9" fill="var(--ink-steel)"/>
        </svg>
        <span>Lindental/Austria</span>
      </div>
      <div class="contact">
        <svg class="contact__icon" viewBox="0 0 14 14" aria-hidden="true">
          <circle cx="7" cy="7" r="7" fill="var(--ink-steel)"/>
          <rect x="3.5" y="4.5" width="7" height="5" fill="none" stroke="#fff" stroke-width="0.9"/>
          <path d="M3.5 4.5 7 7.3l3.5-2.8" fill="none" stroke="#fff" stroke-width="0.9"/>
        </svg>
        <span>info@brennwaldpartner.com</span>
      </div>
      <div class="contact">
        <svg class="contact__icon" viewBox="0 0 14 14" aria-hidden="true">
          <circle cx="7" cy="7" r="7" fill="var(--ink-steel)"/>
          <circle cx="7" cy="7" r="3.6" fill="none" stroke="#fff" stroke-width="0.9"/>
          <path d="M3.4 7h7.2M7 3.4c-1.6 2-1.6 5.2 0 7.2M7 3.4c1.6 2 1.6 5.2 0 7.2" fill="none" stroke="#fff" stroke-width="0.8"/>
        </svg>
        <span>brennwaldpartner.com</span>
      </div>
    </div>
  </article>

  <article class="card card--front" aria-label="Business card front">
    <div class="front__wordmark">Brennwald+Partner</div>
    <div class="front__person">
      <div class="person__name">Example Name</div>
      <div class="person__role">Designation</div>
    </div>
    <p class="front__tagline">We are sparring partners for successful hotels</p>
  </article>

</body>
</html>
```